Heron Loan Partners Business Card

We need a business card design for our mortgage servicing company. In addition to servicing the loans of homeowners, we help homeowners with purchasing their homes and any mortgage refinancing. We would like to see designs that use the colors in the logo attached below (gold-ish yellow and navy blue), and any other design you deem fit! The design should communicate a simpler life with smart mortgages provided by Heron.

```html
<!DOCTYPE html>
<html lang="en">
<head>
<meta charset="UTF-8">
<title>Heron Loan Partners Business Card</title>
<link rel="stylesheet" href="https://fonts.googleapis.com/css2?family=Montserrat:wght@400;600&display=swap">
<style>
  :root {
    --backdrop: #559bb5;
    --card: #ffffff;
    --navy: #25234f;
    --gold: #e0ae3a;
  }
  html, body {
    margin: 0;
    padding: 0;
    width: 1008px;
    height: 1200px;
    overflow: hidden;
    background: var(--backdrop);
    font-family: "Montserrat", sans-serif;
  }
  .card {
    position: absolute;
    left: 114px;
    width: 776px;
    height: 444px;
    background: var(--card);
  }
  .card--front { top: 114px; }
  .card--back { top: 623px; }

  .brand {
    position: absolute;
    left: 0;
    right: 0;
    display: flex;
    align-items: center;
    justify-content: center;
    gap: 14px;
    color: var(--gold);
    font-weight: 600;
    letter-spacing: 0.02em;
    white-space: nowrap;
  }
  .brand__dot {
    width: 18px;
    height: 18px;
    border-radius: 50%;
    background: var(--navy);
  }
  .card--front .brand { top: 150px; font-size: 44px; }
  .card--back .brand { top: 192px; font-size: 48px; }

  .divider {
    position: absolute;
    left: 50px;
    top: 341px;
    width: 680px;
    height: 2px;
    background: var(--gold);
  }
  .person {
    position: absolute;
    left: 50px;
    top: 360px;
    color: var(--navy);
  }
  .person__name {
    font-size: 24px;
    line-height: 1;
    letter-spacing: 0.01em;
  }
  .person__first { font-weight: 600; }
  .person__last { font-weight: 400; }
  .person__role {
    margin-top: 6px;
    font-size: 17px;
    line-height: 1;
  }
  .contact {
    position: absolute;
    right: 46px;
    top: 360px;
    color: var(--navy);
    font-size: 24px;
    line-height: 1;
    text-align: right;
  }
  .contact__row {
    display: flex;
    align-items: center;
    justify-content: flex-end;
    gap: 4px;
    margin-bottom: 6px;
  }
  .contact__icon { width: 18px; height: 18px; }

  .website {
    position: absolute;
    left: 0;
    right: 0;
    top: 372px;
    text-align: center;
    color: var(--gold);
    font-size: 22px;
    letter-spacing: 0.62em;
    padding-left: 0.62em;
    white-space: nowrap;
  }
</style>
</head>
<body>
  <section class="card card--front">
    <div class="brand"><span class="brand__dot"></span>Heron Loan Partners</div>
    <div class="divider"></div>
    <div class="person">
      <div class="person__name"><span class="person__first">DANIEL</span><span class="person__last">WHITCOMBE</span></div>
      <div class="person__role">OWNER</div>
    </div>
    <div class="contact">
      <div class="contact__row">
        <span>hello@heronloans.com</span>
        <svg class="contact__icon" viewBox="0 0 18 18" aria-hidden="true">
          <circle cx="9" cy="9" r="9" fill="var(--gold)"/>
          <rect x="4" y="5.5" width="10" height="7" rx="1" fill="#fff"/>
          <path d="M4.5 6 L9 9.5 L13.5 6" fill="none" stroke="var(--gold)" stroke-width="1.3"/>
        </svg>
      </div>
      <div class="contact__row">
        <span>555-014-2273</span>
        <svg class="contact__icon" viewBox="0 0 18 18" aria-hidden="true">
          <circle cx="9" cy="9" r="9" fill="var(--gold)"/>
          <path d="M6 4.5 C4 6.5 5 10 7.5 12.2 C10 14.3 12.5 14.5 13.6 12.6 L11.8 11 L10.5 12 C9 11.2 7.2 9.4 6.5 7.6 L7.6 6.5 Z" fill="#fff"/>
        </svg>
      </div>
    </div>
  </section>

  <section class="card card--back">
    <div class="brand"><span class="brand__dot"></span>Heron Loan Partners</div>
    <div class="website">www.heronloanpartners.com</div>
  </section>
</body>
</html>
```